Personal website for my flying adventures

It is the website for my personal flying adventures.

1. I flew around the world in 2011 and became the first Chinese citizen ever flying the single engine airplane around the world in the history and also the first ever to land the single engine airplane in Halvern Ridge airport.
2. I am organizing the "Copper Kestrels Aerobatic Flying Team" in China
3. I am sharing my flying experiences regularly
4. I am writing the book about flying around the world.

Visit: www.lutanmo.com and www.tanmoskyloop.com for more information and pictures on my flying activities. Need connect two websites together well.

Target Market(s)

Young pilots

Industry/Entity Type

Airport

Requirements
Must have
• Must have the logo of "Tanmo Sky Loop"
• Must have the logo of "Copper Kestrels"
• Must have my flying pictures

```html
<!DOCTYPE html>
<html lang="en">
<head>
<meta charset="utf-8">
<title>Tanmo Sky Loop</title>
<link href="https://fonts.googleapis.com/css2?family=PT+Sans:wght@400;700&family=PT+Sans+Narrow:wght@400;700&display=swap" rel="stylesheet">
<style>
:root{
  --sky:#2aa7dd;
  --sky-deep:#1a8fcb;
  --sky-light:#6cc7ee;
  --red:#d5232b;
  --ink:#333;
  --muted:#555;
  --panel:#f5f5f5;
  --white:#fff;
  --night:#050505;
}
*{box-sizing:border-box;margin:0;padding:0}
html,body{width:886px;height:1200px;overflow:hidden}
body{position:relative;font-family:"PT Sans",sans-serif;color:var(--ink);
  background:linear-gradient(180deg,var(--sky-deep) 0,var(--sky) 400px,var(--sky-light) 1110px)}
.abs{position:absolute}
.cond{font-family:"PT Sans Narrow",sans-serif}

/* header */
.header{left:0;top:0;width:886px;height:148px}
.brand{left:110px;top:18px;width:110px;text-align:center}
.brand-mark{width:76px;height:76px;border-radius:50%;background:var(--sky);margin:0 auto 4px}
.brand-name{font-weight:700;font-size:12px;color:var(--red);line-height:1.1}
.brand-url{font-weight:700;font-size:10px;color:var(--red);margin-top:6px}
.lang{left:458px;top:35px;width:113px;height:20px;border:1px solid #aaa;background:#fff;font-size:8.5px;color:#999;padding:4px 0 0 27px;font-style:italic}
.lang::before{content:"";position:absolute;left:6px;top:5px;width:14px;height:9px;background:#2d4e9c}
.lang::after{content:"⌄";position:absolute;right:6px;top:0;font-size:10px;color:#555;font-style:normal}
.search{left:590px;top:35px;width:186px;height:22px;border:1px solid #aaa;border-radius:4px;background:#fff;font-size:9px;color:#888;padding:5px 0 0 33px}
.search svg{position:absolute;left:9px;top:4px}
.search-go{position:absolute;right:-1px;top:-1px;width:32px;height:22px;background:var(--sky);color:#fff;border-radius:0 4px 4px 0;font-size:9px;text-align:center;line-height:22px}
.nav{left:331px;top:90px;display:flex;font-size:10px;color:#222}
.nav a{color:inherit;text-decoration:none;height:24px;line-height:24px;padding:0 11px;border-right:1px solid #e6e6e6}
.nav a:last-child{border-right:0}
.nav .is-active{background:var(--red);color:#fff;border-radius:2px;padding:0 12px;margin-right:0}

/* hero */
.hero{left:84px;top:143px;width:719px;height:298px;background:#fff;box-shadow:0 8px 14px rgba(0,0,0,.18)}
.hero-photo{left:13px;top:13px;width:696px;height:273px;background:linear-gradient(100deg,#8d8a80 0,#b7b2a5 40%,#d7d3cc 70%,#9a9ba0 100%)}
.hero-caption{left:13px;top:13px;width:173px;height:273px;background:rgba(40,40,40,.72);color:#fff;padding:93px 0 0 16px;font-family:"PT Sans Narrow",sans-serif;font-weight:700;font-size:16px;line-height:22px}
.hero-caption p+p{margin-top:22px;font-size:13.5px}
.hero-arrow{top:128px;width:22px;height:24px;background:#555;color:#fff;font-size:9px;line-height:24px;text-align:center}
.hero-arrow.prev{left:0;border-radius:0 12px 12px 0}
.hero-arrow.next{right:0;border-radius:12px 0 0 12px}

/* main panel */
.main{left:81px;top:484px;width:724px;height:620px;background:var(--panel);border-radius:6px;border:1px solid #dcdcdc}
.itinerary{left:81px;top:465px;width:279px;height:287px;background:#fff;border:1px solid #ddd;border-radius:4px 4px 0 0;box-shadow:2px 2px 4px rgba(0,0,0,.08)}
.itinerary h2{position:absolute;left:12px;top:10px;font-family:"PT Sans Narrow",sans-serif;font-size:14px;color:var(--sky);font-weight:700}
.itinerary .toggle{position:absolute;right:8px;top:14px;font-size:8px;line-height:6px;color:#555}
.itin-table{position:absolute;left:1px;top:38px;width:277px;border-collapse:collapse;font-size:9px;color:#444}
.itin-table th{font-family:"PT Sans Narrow",sans-serif;font-size:12px;color:var(--red);text-align:left;font-weight:700;height:20px;border-bottom:1px solid #ddd}
.itin-table td{height:45px;vertical-align:top;padding-top:9px;border-bottom:1px solid #ddd;line-height:13px}
.itin-table tr:nth-child(even) td{background:#f7f7f7}
.itin-table .c-day{padding-left:12px;width:50px}
.itin-table td.c-day{padding-top:14px}
.download{left:92px;top:762px;width:260px;height:41px;border:1px solid #bbb;border-radius:3px;background:linear-gradient(#f5f5f5,#d9d9d9);font-family:"PT Sans Narrow",sans-serif;font-size:14px;color:#222;padding:11px 0 0 57px}
.download-icon{position:absolute;left:10px;top:4px;width:34px;height:32px;background:var(--red);border-radius:3px}

.welcome-title{left:385px;top:501px;font-family:"PT Sans Narrow",sans-serif;font-weight:700;font-size:15px;color:#333}
.welcome-title span{color:var(--sky)}
.rule{left:387px;top:525px;width:407px;border-top:1px dotted #999}
.welcome-photo{left:392px;top:542px;width:136px;height:100px;border:4px solid #fff;box-shadow:2px 2px 4px rgba(0,0,0,.35);transform:rotate(-3deg);background:linear-gradient(180deg,#8fb6dc,#c5b49a)}
.welcome-text{left:541px;top:536px;width:254px;font-size:9.3px;line-height:15.5px;text-align:justify;color:#444}
.btn-more{left:544px;top:670px;width:61px;height:24px;background:var(--sky);color:#fff;border-radius:2px;font-family:"PT Sans Narrow",sans-serif;font-weight:700;font-size:12px;text-align:center;line-height:24px}

.sponsors{left:387px;top:720px;width:395px;height:89px;background:#fff;border:1px solid #ddd;border-radius:3px}
.sponsors h3{position:absolute;left:21px;top:12px;font-family:"PT Sans Narrow",sans-serif;font-weight:400;font-size:14px;color:#222}
.sponsors .pager{position:absolute;right:8px;top:10px;color:var(--sky);font-size:13px}
.sponsor-list{position:absolute;left:14px;top:42px;display:flex;gap:14px;align-items:center}
.sponsor{display:flex;align-items:center;gap:4px;font-size:10px;font-weight:700;color:#2a6fb0;white-space:nowrap}
.sponsor i{display:block;width:12px;height:12px;background:currentColor;border-radius:50%}
.sponsor.red{color:var(--red)}
.sponsor.plate{background:#2a90c8;color:#fff;padding:8px 6px}
.sponsor.plate i{background:#fff}

/* cards */
.card{width:198px;height:216px}
.card-box{position:absolute;left:0;top:31px;width:198px;height:191px;background:#fff;border:1px solid #ddd;border-radius:5px;box-shadow:0 1px 3px rgba(0,0,0,.1)}
.card-tab{position:absolute;left:0;top:0;width:151px;height:31px;background:var(--sky);border-radius:4px 4px 0 0;color:#fff;font-family:"PT Sans Narrow",sans-serif;font-weight:700;font-size:12px;padding:9px 0 0 9px}
.card-media{position:absolute;left:7px;top:40px;width:184px;height:85px;border:2px solid #4f9fd8;border-radius:3px}
.card-text{position:absolute;left:10px;top:132px;width:180px;font-size:8.3px;line-height:13.3px;color:#444}
.card-text.justify{text-align:justify}
.card-more{position:absolute;right:-1px;bottom:-7px;width:66px;height:26px;background:var(--sky);color:#fff;border-radius:4px 0 4px 0;font-size:8.5px;line-height:26px;padding-left:15px}
.card-more::after{content:"›";position:absolute;right:8px;top:7px;width:12px;height:12px;background:#1b3c5c;border-radius:50%;font-size:10px;line-height:11px;text-align:center}
.video{background:linear-gradient(180deg,#3a5d96,#1e3868)}
.video-brand{position:absolute;left:14px;top:6px;font-size:14px;color:#fff}
.video-note{position:absolute;left:16px;top:30px;font-size:8px;color:#dde;letter-spacing:1px}
.video-bar{position:absolute;left:0;bottom:0;width:100%;height:12px;background:#0c1e3d}
.video-play{position:absolute;left:72px;top:20px;width:40px;height:36px;background:rgba(255,255,255,.3);border-radius:3px}
.kestrel-logo{display:flex;align-items:center;justify-content:center;gap:6px;font-size:13px;font-weight:700;color:#1f3c6b}
.kestrel-logo i{width:14px;height:14px;background:#1f3c6b;border-radius:50%}

/* footer */
.footer{left:0;top:1122px;width:886px;height:78px}
.social{left:86px;top:1152px;display:flex;gap:12px}
.social span{width:16px;height:16px;border-radius:2px}
.copyright{right:82px;top:1153px;font-size:7.5px;color:#ddd}
</style>
</head>
<body>

<svg class="abs header" viewBox="0 0 886 148" role="presentation">
  <rect x="0" y="0" width="886" height="7" fill="#2aa7dd"/>
  <path d="M0 9 L40 8 L80 10 L140 7 L220 10 L300 8 L400 11 L520 8 L640 10 L760 8 L886 10 L886 128 L840 131 L800 127 L760 132 L700 128 L640 133 L560 128 L480 132 L400 127 L320 133 L240 128 L160 132 L90 127 L40 131 L0 128 Z" fill="#fff"/>
</svg>

<div class="abs brand">
  <div class="brand-mark"></div>
  <div class="brand-name">Tanmo Sky Loop</div>
  <div class="brand-url">WWW.LUTANMO.COM</div>
</div>

<div class="abs lang">English</div>
<div class="abs search">
  <svg width="14" height="14" viewBox="0 0 14 14"><circle cx="6" cy="6" r="4.2" fill="none" stroke="#777" stroke-width="1.6"/><line x1="9" y1="9" x2="13" y2="13" stroke="#777" stroke-width="1.8"/></svg>
  Search
  <span class="search-go">GO</span>
</div>

<nav class="abs nav">
  <a class="is-active" href="#">Home</a>
  <a href="#">The Expedition</a>
  <a href="#">Media Room</a>
  <a href="#">Sponsors</a>
  <a href="#">Tanmo Tracker</a>
  <a href="#">Contests</a>
  <a href="#">Store</a>
</nav>

<section class="abs hero">
  <div class="abs hero-photo" role="img" aria-label="Pilot in uniform beside his single engine airplane at the airport"></div>
  <div class="abs hero-caption">
    <p>DAY 69: MEMPHIS,<br>TN U.S.A.!</p>
    <p>THANK EVERYONE FOR YOUR<br>SUPPORT AND LOVE!</p>
  </div>
  <div class="abs hero-arrow prev">«</div>
  <div class="abs hero-arrow next">»</div>
</section>

<div class="abs main"></div>

<section class="abs itinerary">
  <h2>FLIGHT ITINERARY</h2>
  <div class="toggle">˄<br>˅</div>
  <table class="itin-table">
    <tr><th class="c-day">DAY</th><th style="width:50px">DATE</th><th style="width:97px">DEPART FROM</th><th>ARRIVE AT</th></tr>
    <tr><td class="c-day">1</td><td>Sunday,<br>May 22</td><td>Memphis, USA</td><td>Washington<br>DC, USA</td></tr>
    <tr><td class="c-day">2</td><td>Monday,<br>May 22</td><td>Memphis, USA</td><td>Washington<br>DC, USA</td></tr>
    <tr><td class="c-day">3</td><td>Tuesday,<br>May 22</td><td>Memphis, USA</td><td>Washington<br>DC, USA</td></tr>
    <tr><td class="c-day">4</td><td>Wed-day,<br>May 22</td><td>Memphis, USA</td><td>Washington<br>DC, USA</td></tr>
    <tr><td class="c-day">5</td><td>Thursday,<br>May 22</td><td>Memphis, USA</td><td>Washington<br>DC, USA</td></tr>
  </table>
</section>

<div class="abs download"><span class="download-icon"></span>Download Latest Flight Itinerary</div>

<h2 class="abs welcome-title">Welcome to <span>Tanmo Sky Loop</span></h2>
<div class="abs rule"></div>
<div class="abs welcome-photo" role="img" aria-label="Pilot wearing headset and sunglasses in the cockpit"></div>
<p class="abs welcome-text">I love to fly, and enjoy the flight to bring happiness and convenience. In China, we think that the private flight is rich play of the game, in the United States, the performance of the overall national strength. With the development of general aviation in China, Chinese people will enjoy the freedoms and rights of the flight. I hope that through the love of my flight, to promote the development of China's general aviation, and promote the development of China!</p>
<div class="abs btn-more">More</div>

<section class="abs sponsors">
  <h3>SPONSORS</h3>
  <span class="pager">( )</span>
  <div class="sponsor-list">
    <span class="sponsor red"><i></i>Meridian Daily</span>
    <span class="sponsor"><i></i>Lanting Web</span>
    <span class="sponsor plate"><i></i>Lanting Micro</span>
    <span class="sponsor" style="color:#3b4a7a"><i></i>The Harwell</span>
  </div>
</section>

<article class="abs card" style="left:102px;top:848px">
  <div class="card-box">
    <div class="card-media" style="top:9px;background:linear-gradient(180deg,#4a78b8,#c9d6e6 60%,#eef2f6)" role="img" aria-label="Single engine airplane flying above the clouds"></div>
    <p class="card-text justify" style="top:101px">The first round-the-world flight in a single engine airplane took place in 1919. There have been people from 28 countries who have successfully achieved the challenge.</p>
    <span class="card-more">MORE</span>
  </div>
  <div class="card-tab">THE EXPEDITION</div>
</article>

<article class="abs card" style="left:341px;top:854px">
  <div class="card-box">
    <div class="card-media video" style="top:9px" role="img" aria-label="Video player showing an unavailable clip">
      <span class="video-brand">Reelcast</span>
      <span class="video-note">THIS VIDEO IS NOT CURRENTLY AVAILABLE</span>
      <span class="video-play"></span>
      <span class="video-bar"></span>
    </div>
    <p class="card-text" style="top:101px">Memphis Pilot to Fly Around the World<br>There have been people from 28 countries who have successfully achieved the challenge.</p>
    <span class="card-more">MORE</span>
  </div>
  <div class="card-tab">VIDEOS</div>
</article>

<article class="abs card" style="left:578px;top:854px">
  <div class="card-box">
    <div class="card-media kestrel-logo" style="top:9px"><i></i>Copper Kestrels</div>
    <p class="card-text" style="top:101px">Uenim ad minim veniam, quis laboris nisi utaliquipveniam, quis quis laboris nisi utaliquip Uenim ad minim veniam, quis laboris nisi utaliquipveniam.</p>
    <span class="card-more">MORE</span>
  </div>
  <div class="card-tab">COPPER KESTRELS</div>
</article>

<svg class="abs footer" viewBox="0 0 886 78" role="presentation">
  <path d="M0 8 L7 0 L14 8 L21 0 L28 8 L35 0 L42 8 L49 0 L56 8 L63 0 L70 8 L77 0 L84 8 L91 0 L98 8 L105 0 L112 8 L119 0 L126 8 L133 0 L140 8 L147 0 L154 8 L161 0 L168 8 L175 0 L182 8 L189 0 L196 8 L203 0 L210 8 L217 0 L224 8 L231 0 L238 8 L245 0 L252 8 L259 0 L266 8 L273 0 L280 8 L287 0 L294 8 L301 0 L308 8 L315 0 L322 8 L329 0 L336 8 L343 0 L350 8 L357 0 L364 8 L371 0 L378 8 L385 0 L392 8 L399 0 L406 8 L413 0 L420 8 L427 0 L434 8 L441 0 L448 8 L455 0 L462 8 L469 0 L476 8 L483 0 L490 8 L497 0 L504 8 L511 0 L518 8 L525 0 L532 8 L539 0 L546 8 L553 0 L560 8 L567 0 L574 8 L581 0 L588 8 L595 0 L602 8 L609 0 L616 8 L623 0 L630 8 L637 0 L644 8 L651 0 L658 8 L665 0 L672 8 L679 0 L686 8 L693 0 L700 8 L707 0 L714 8 L721 0 L728 8 L735 0 L742 8 L749 0 L756 8 L763 0 L770 8 L777 0 L784 8 L791 0 L798 8 L805 0 L812 8 L819 0 L826 8 L833 0 L840 8 L847 0 L854 8 L861 0 L868 8 L875 0 L882 8 L886 4 L886 78 L0 78 Z" fill="#050505"/>
</svg>

<div class="abs social">
  <span style="background:#3b5a9a" aria-label="Social link"></span>
  <span style="background:#2f9fd8" aria-label="Social link"></span>
  <span style="background:#2a77b4" aria-label="Social link"></span>
  <span style="background:#f08a1d" aria-label="Feed link"></span>
</div>
<p class="abs copyright">© 2013 tanmoskyloop.com, All Rights Reserved</p>

</body>
</html>
```